Square graphic for social media post

I want to create a 1080 x 1080px all-black image for the quote below that I can share on social media. I want the emphasis to be primarily on the quote, secondarily on the portrait, and third (smallest) on the logo. I want the background on the portrait to be edited so it's transparent and just shows the face of the person on a black background (no brick wall visible).

Graphic color: black
Text color: white
Content: "What we went through is going to make the greatest generation of hoteliers our industry has ever seen." << biggest text
Derek Holm << smaller text
President, Silverbrook Hotels << smaller text
[image of person - use whichever version looks better to you]
[Add Lodging Ledger logo - whichever looks better to you]

This image needs to be readable when sized down much smaller (400x400?) so want the text and portrait to take up most of the space.

I'd like the output both as PNG and original file (preferably Canva). Thanks!

Target Market(s)

Hotel managers

Industry/Entity Type

Hospitality

Font styles to use
Sans Serif

Colors

Designer to choose colors to be used in the design.

Requirements
Must have
• Needs to focus on the quote and the person quoted (the portrait)

```html
<!DOCTYPE html>
<html lang="en">
<head>
<meta charset="utf-8">
<title>Quote Card – Derek Holm</title>
<link href="https://fonts.googleapis.com/css2?family=Bebas+Neue&family=Open+Sans:wght@400;700&display=swap" rel="stylesheet">
<style>
  :root {
    --bg: #000000;
    --ink: #ffffff;
    --quote-mark: #2a2a2a;
    --portrait-top: #d9d6d2;
    --portrait-bottom: #1f3566;
  }
  * { margin: 0; padding: 0; box-sizing: border-box; }
  html, body { width: 1200px; height: 1200px; overflow: hidden; background: var(--bg); }
  .card {
    position: relative;
    width: 1200px;
    height: 1200px;
    background: var(--bg);
    color: var(--ink);
  }
  .quote-mark {
    position: absolute;
    width: 82px;
    height: 82px;
    border-radius: 50%;
    background: var(--quote-mark);
    color: #000;
    font-family: Georgia, serif;
    font-size: 84px;
    font-weight: 700;
    line-height: 1;
    text-align: center;
    padding-top: 16px;
  }
  .quote-mark--open { left: 76px; top: 86px; }
  .quote-mark--close { left: 498px; top: 862px; }
  .quote-text {
    position: absolute;
    left: 120px;
    top: 124px;
    width: 900px;
    font-family: "Bebas Neue", sans-serif;
    font-size: 115px;
    line-height: 104px;
    letter-spacing: 0.5px;
    text-transform: uppercase;
  }
  .quote-text span { display: block; }
  .brand {
    position: absolute;
    left: 140px;
    top: 1010px;
    width: 320px;
    text-align: center;
    font-family: "Bebas Neue", sans-serif;
    font-size: 48px;
    letter-spacing: 8px;
  }
  .connector { position: absolute; left: 0; top: 0; }
  .portrait {
    position: absolute;
    left: 797px;
    top: 728px;
    width: 272px;
    height: 272px;
    border-radius: 50%;
    border: 6px solid var(--ink);
    background: linear-gradient(180deg, var(--portrait-top) 0%, var(--portrait-top) 55%, var(--portrait-bottom) 100%);
  }
  .speaker-name {
    position: absolute;
    left: 578px;
    top: 1030px;
    font-family: "Bebas Neue", sans-serif;
    font-size: 66px;
    line-height: 1;
  }
  .speaker-role {
    position: absolute;
    left: 842px;
    top: 1028px;
    font-family: "Open Sans", sans-serif;
  }
  .speaker-title { font-size: 27px; font-weight: 700; line-height: 1.1; }
  .speaker-company { font-size: 20px; font-weight: 400; line-height: 1.3; margin-left: 3px; }
</style>
</head>
<body>
  <main class="card">
    <div class="quote-mark quote-mark--open" aria-hidden="true">&ldquo;</div>
    <blockquote class="quote-text">
      <span>What we went</span>
      <span>through is going</span>
      <span>to make the</span>
      <span>greatest generation</span>
      <span>of hoteliers our</span>
      <span>industry has</span>
      <span>ever seen</span>
    </blockquote>
    <div class="quote-mark quote-mark--close" aria-hidden="true">&rdquo;</div>

    <div class="brand">Lodging Ledger</div>

    <svg class="connector" width="1200" height="1200" viewBox="0 0 1200 1200" aria-hidden="true">
      <line x1="542" y1="1003" x2="830" y2="1003" stroke="#ffffff" stroke-width="4"/>
      <circle cx="542" cy="1003" r="9" fill="#000" stroke="#ffffff" stroke-width="4"/>
    </svg>

    <div class="portrait" role="img" aria-label="Portrait photo of Derek Holm, smiling, wearing a navy blazer and white shirt"></div>

    <div class="speaker-name">Derek Holm</div>
    <div class="speaker-role">
      <div class="speaker-title">President</div>
      <div class="speaker-company">Silverbrook Hotels</div>
    </div>
  </main>
</body>
</html>
```